New Business Card Design

We would like to refresh our business cards and make them look better. We are an IT company specialising in Cloud Services, IT Managed Services, software and hardware. I have attached a PSD of our current design. Also attached our logo.
Updates

I have uploaded all new logos in EPS format.

Can you please edit all designs to include a job title for Marcus Hollis, eg. General Manager

Industry/Entity Type

Software

Colors
ffffff

Requirements
Must have
• Please use white background.
Should not have
• Black background

```html
<!DOCTYPE html>
<html lang="en">
<head>
<meta charset="utf-8">
<title>Meridian Systems – Business Card</title>
<link rel="stylesheet" href="https://fonts.googleapis.com/css2?family=Open+Sans:wght@400;600;700&display=swap">
<style>
  :root {
    --stage: #e8e8eb;
    --brand-red: #c0392b;
    --navy: #1f2a36;
    --steel: #9ea3aa;
    --ink: #2b2e33;
    --paper: #ffffff;
  }
  * { box-sizing: border-box; margin: 0; padding: 0; }
  html, body {
    width: 1200px; height: 987px; overflow: hidden;
    background: var(--stage);
    font-family: "Open Sans", Arial, sans-serif;
  }
  .canvas { position: relative; width: 1200px; height: 987px; }
  .card {
    position: absolute; left: 270px; width: 660px; height: 377px;
    border-radius: 28px; overflow: hidden;
    box-shadow: 0 6px 18px rgba(0,0,0,.12);
  }
  .card--front { top: 78px; background: var(--paper); }
  .card--back { top: 532px; background: var(--brand-red); color: var(--paper); }
  .card__wave { position: absolute; inset: 0; z-index: 0; }

  .brand {
    position: absolute; left: 140px; top: 88px; z-index: 1;
    display: flex; align-items: center; gap: 18px; white-space: nowrap;
  }
  .brand__mark { width: 60px; height: 60px; border-radius: 50%; background: var(--brand-red); flex: none; }
  .brand__name { font-size: 40px; font-weight: 400; letter-spacing: 3px; color: var(--ink); }

  .holder { position: absolute; left: 30px; top: 244px; z-index: 1; color: var(--paper); white-space: nowrap; }
  .holder__name { font-size: 19px; font-weight: 700; font-family: "Open Sans", Arial, sans-serif; }
  .holder__role { font-size: 13px; margin-top: 2px; }

  .contacts {
    position: absolute; left: 230px; top: 302px; z-index: 1;
    display: grid; grid-template-columns: auto auto; column-gap: 34px; row-gap: 10px;
    color: var(--paper); font-size: 15px;
  }
  .contact { display: flex; align-items: center; gap: 8px; white-space: nowrap; }
  .contact svg { width: 16px; height: 16px; flex: none; }

  .back__mark {
    position: absolute; left: 280px; top: 58px;
    width: 100px; height: 100px; border-radius: 50%; background: var(--paper);
  }
  .back__tagline {
    position: absolute; left: 0; right: 0; top: 200px;
    text-align: center; font-size: 19px; line-height: 1.45;
  }
  .back__web {
    position: absolute; left: 0; right: 0; top: 290px;
    text-align: center; font-size: 14px; letter-spacing: 4px;
  }
  .back__web b { font-weight: 700; }
</style>
</head>
<body>
<main class="canvas">

  <section class="card card--front" aria-label="Card front">
    <svg class="card__wave" viewBox="0 0 660 377" aria-hidden="true">
      <path d="M0,94 C40,214 200,234 330,234 C470,234 580,229 660,254 L660,377 L0,377 Z" fill="var(--steel)"/>
      <path d="M0,100 C40,220 200,240 330,240 C470,240 580,235 660,260 L660,377 L0,377 Z" fill="var(--paper)"/>
      <path d="M0,104 C40,224 200,244 330,244 C470,244 580,239 660,264 L660,377 L0,377 Z" fill="var(--navy)"/>
      <path d="M0,110 C40,230 200,250 330,250 C470,250 580,245 660,270 L660,377 L0,377 Z" fill="var(--brand-red)"/>
    </svg>

    <div class="brand">
      <span class="brand__mark"></span>
      <span class="brand__name">Meridian Systems</span>
    </div>

    <div class="holder">
      <p class="holder__name">Marcus Hollis</p>
      <p class="holder__role">General Manager</p>
    </div>

    <div class="contacts">
      <p class="contact">
        <svg viewBox="0 0 16 16"><rect x="1" y="3.5" width="14" height="9" rx="1.5" fill="none" stroke="#fff" stroke-width="1.4"/><path d="M1.5 4.5 L8 9 L14.5 4.5" fill="none" stroke="#fff" stroke-width="1.4"/></svg>
        mhollis@meridiansys.com.au
      </p>
      <p class="contact">
        <svg viewBox="0 0 16 16"><path d="M4 1.5 L6.5 4.5 L5 6 C6 8.5 7.5 10 10 11 L11.5 9.5 L14.5 12 L12.5 14.5 C7 14 2 9 1.5 3.5 Z" fill="#fff"/></svg>
        07 3000 4821
      </p>
      <p class="contact">
        <svg viewBox="0 0 16 16"><circle cx="8" cy="8" r="6.5" fill="none" stroke="#fff" stroke-width="1.3"/><ellipse cx="8" cy="8" rx="3" ry="6.5" fill="none" stroke="#fff" stroke-width="1.1"/><path d="M1.5 8 H14.5" stroke="#fff" stroke-width="1.1"/></svg>
        www.meridiansys.com.au
      </p>
      <p class="contact">
        <svg viewBox="0 0 16 16"><rect x="4" y="1" width="8" height="14" rx="1.5" fill="none" stroke="#fff" stroke-width="1.4"/><rect x="5.5" y="3" width="5" height="6" fill="#fff"/></svg>
        0400 555 172
      </p>
    </div>
  </section>

  <section class="card card--back" aria-label="Card back">
    <span class="back__mark"></span>
    <p class="back__tagline">We are an IT company specializing in Cloud Services<br>IT Managed Services, software and hardware</p>
    <p class="back__web">www.<b>meridiansys</b>.com.au</p>
  </section>

</main>
</body>
</html>
```